A start up Private Wine Label for export to Asia.

We are looking for the best graphic design for our very first wine label Corvessa Wines and would like the following requirements:

1. Black background - explore and play around the shade of black
2. Gold Shimmery Colour Font
3. Font should be a cursive classic posh that says Corvessa Wines
4. We would like the front graphic design to be simple and elegant and has a traditional classic feel to it.

Target Market(s)

Small scale to test the upper class market for export to Asia

Font styles to use
Script

Colors

Designer to choose colors to be used in the design.

Requirements
Must have
• Gold font for the label Corvessa Wines with shimmery touch to it.
• Elegant black background.
• Simple but elegant design.
• Attractive to the upper class market in Asia.
Nice to have
• Explore and play around with your imagination.

```html
<!DOCTYPE html>
<html lang="en">
<head>
<meta charset="utf-8">
<title>Corvessa Wines – Label</title>
<link rel="stylesheet" href="https://fonts.googleapis.com/css2?family=Great+Vibes&display=swap">
<style>
  :root {
    --page-white: #ffffff;
    --label-black: #000000;
    --label-glow: #1d1d1d;
    --gold: #d9b347;
    --gold-deep: #9c6e2c;
    --gold-soft: #c99a55;
  }
  html, body {
    margin: 0;
    padding: 0;
    width: 1200px;
    height: 1200px;
    overflow: hidden;
    background: var(--page-white);
  }
  .canvas {
    position: relative;
    width: 1200px;
    height: 1200px;
  }
  .label {
    position: absolute;
    left: 236px;
    top: 222px;
    width: 728px;
    height: 718px;
    background: radial-gradient(ellipse at 50% 50%, var(--label-glow) 0%, #0b0b0b 45%, var(--label-black) 80%);
    overflow: hidden;
  }
  .ornament {
    position: absolute;
    left: 104px;
    width: 530px;
    height: 160px;
  }
  .ornament--top { top: 0; }
  .ornament--bottom { bottom: 0; }
  .ornament svg { display: block; width: 100%; height: 100%; }
  .wordmark {
    position: absolute;
    left: 0;
    width: 100%;
    text-align: center;
    font-family: "Great Vibes", cursive;
    color: var(--gold);
    margin: 0;
    font-weight: 400;
    line-height: 1;
  }
  .wordmark__name {
    top: 262px;
    font-size: 132px;
    letter-spacing: 1px;
  }
  .wordmark__kind {
    top: 400px;
    font-size: 62px;
    color: var(--gold-soft);
  }
</style>
</head>
<body>
<div class="canvas">
  <section class="label">
    <div class="ornament ornament--top" role="img" aria-label="Gold lace mandala ornament hanging from the top edge">
      <svg viewBox="0 0 530 160" preserveAspectRatio="none">
        <defs>
          <linearGradient id="ornament-gold-top" x1="0" y1="0" x2="1" y2="0">
            <stop offset="0" stop-color="#9c6e2c" stop-opacity="0.35"/>
            <stop offset="0.5" stop-color="#e2b86a" stop-opacity="0.55"/>
            <stop offset="1" stop-color="#9c6e2c" stop-opacity="0.35"/>
          </linearGradient>
        </defs>
        <polygon points="0,0 530,0 530,50 400,60 330,110 265,160 200,110 130,60 0,50" fill="url(#ornament-gold-top)"/>
      </svg>
    </div>

    <h1 class="wordmark wordmark__name">Corvessa</h1>
    <p class="wordmark wordmark__kind">Wines</p>

    <div class="ornament ornament--bottom" role="img" aria-label="Gold lace mandala ornament rising from the bottom edge">
      <svg viewBox="0 0 530 160" preserveAspectRatio="none">
        <defs>
          <linearGradient id="ornament-gold-bottom" x1="0" y1="0" x2="1" y2="0">
            <stop offset="0" stop-color="#9c6e2c" stop-opacity="0.35"/>
            <stop offset="0.5" stop-color="#e2b86a" stop-opacity="0.55"/>
            <stop offset="1" stop-color="#9c6e2c" stop-opacity="0.35"/>
          </linearGradient>
        </defs>
        <polygon points="0,160 530,160 530,110 400,100 330,50 265,0 200,50 130,100 0,110" fill="url(#ornament-gold-bottom)"/>
      </svg>
    </div>
  </section>
</div>
</body>
</html>
```